Business card design Needed for new logo / Construction business, home extensions and new builds

We need a business card design using our new logo files which i will attach to this project :)

We are a small construction business specialising in home extensions, new builds and property development. We are very ambitious and would appreciate professional and elegant designs for our new business card.

Very serious about using the services on MakerQuarry and recently acquired our new logo from here :)

Please get involved, i will feedback when i can as i am very busy but can respond daily, thanks

Target Market(s)

People that want to build onto their houses, new building developments or adding too their existing property

Industry/Entity Type

Construction

Contact Information for Business Card

Renwick Tolliver Construction, Lionel Ashby (Managing Director), Tel 07822254961, email - info@renwick-tolliver, www.renwick-tolliver.co.uk

Colors

Designer to choose colors to be used in the design.

Requirements
Must have
• I like a deep grey on the back please. A lot of you have provided black from and back, try mixing things up a little. The black looks cool 😎 Thanks

```html
<!DOCTYPE html>
<html lang="en">
<head>
<meta charset="utf-8">
<title>Renwick Tolliver Construction – Business Card</title>
<link rel="stylesheet" href="https://fonts.googleapis.com/css2?family=Open+Sans:wght@400;600;700&display=swap">
<style>
  :root {
    --stage: #232323;
    --card-dark: #1f1f22;
    --card-dark-2: #26262a;
    --card-grey: #8f969d;
    --card-grey-light: #a3a9af;
    --gold: #e8a623;
    --gold-deep: #c98a12;
    --silver: #d2d4d7;
    --white: #f4f4f4;
    --muted-line: rgba(255,255,255,0.75);
  }
  * { box-sizing: border-box; margin: 0; padding: 0; }
  html, body {
    width: 1200px; height: 780px; overflow: hidden;
    background: var(--stage);
    font-family: "Open Sans", Arial, sans-serif;
  }
  .canvas { position: relative; width: 1200px; height: 780px; }

  .card {
    position: absolute;
    width: 560px; height: 320px;
    border-radius: 22px;
    border: 3px solid var(--gold);
    overflow: hidden;
    box-shadow: 0 18px 40px rgba(0,0,0,0.55);
  }

  /* Back side */
  .card-back {
    left: 60px; top: 60px;
    background: linear-gradient(135deg, var(--card-grey-light), var(--card-grey));
  }
  .back-pattern {
    position: absolute; inset: 0;
    background: linear-gradient(160deg, #aab0b6 0%, #959ca3 55%, #878e95 100%);
  }
  .back-brand {
    position: absolute; right: 26px; bottom: 26px;
    display: flex; align-items: center; gap: 7px;
    color: var(--white);
    font-size: 10px; font-weight: 600; letter-spacing: 0.04em;
    text-transform: uppercase;
  }
  .back-brand .brand-dot {
    width: 12px; height: 12px; background: var(--white);
  }

  /* Front side */
  .card-front {
    left: 580px; top: 400px;
    background: linear-gradient(150deg, var(--card-dark-2), var(--card-dark));
    color: var(--white);
  }
  .front-mark {
    position: absolute; left: 190px; top: 40px;
    width: 240px; height: 240px;
    border-radius: 50%;
    background: radial-gradient(circle, rgba(255,255,255,0.05) 0%, rgba(255,255,255,0.02) 60%, rgba(255,255,255,0) 72%);
  }
  .identity {
    position: absolute; left: 40px; top: 116px;
  }
  .name {
    font-size: 34px; font-weight: 700; line-height: 1; letter-spacing: 0.01em;
  }
  .name .first { color: var(--silver); }
  .name .last { color: var(--gold); }
  .role {
    margin-top: 6px; margin-left: 96px;
    font-size: 16px; font-weight: 600; color: var(--white);
  }
  .divider {
    position: absolute; left: 300px; top: 70px;
    width: 1px; height: 130px;
    background: var(--muted-line);
    transform: rotate(-18deg);
  }
  .contacts {
    position: absolute; left: 328px; top: 72px;
    list-style: none;
    display: flex; flex-direction: column; gap: 9px;
    font-size: 14.5px;
  }
  .contacts li { display: flex; align-items: center; gap: 9px; }
  .contacts svg { width: 15px; height: 15px; flex: none; }
  .address {
    position: absolute; left: 40px; bottom: 38px;
    font-size: 16px; letter-spacing: 0.01em;
  }
</style>
</head>
<body>
<main class="canvas">

  <section class="card card-back" aria-label="Card back">
    <div class="back-pattern" role="img" aria-label="Repeating tonal brand pattern on deep grey"></div>
    <div class="back-brand">
      <span class="brand-dot"></span>
      <span>Renwick Tolliver Construction</span>
    </div>
  </section>

  <section class="card card-front" aria-label="Card front">
    <div class="front-mark" role="img" aria-label="Faint large brand mark in the background"></div>

    <div class="identity">
      <p class="name"><span class="first">Lionel</span> <span class="last">Ashby</span></p>
      <p class="role">Managing Director</p>
    </div>

    <span class="divider"></span>

    <ul class="contacts">
      <li>
        <svg viewBox="0 0 24 24" aria-hidden="true"><path fill="#e8a623" d="M6.6 10.8a15 15 0 0 0 6.6 6.6l2.2-2.2a1 1 0 0 1 1-.25 11.4 11.4 0 0 0 3.6.57 1 1 0 0 1 1 1V20a1 1 0 0 1-1 1A17 17 0 0 1 3 4a1 1 0 0 1 1-1h3.5a1 1 0 0 1 1 1c0 1.25.2 2.45.57 3.57a1 1 0 0 1-.25 1z"/></svg>
        <span>0782 225 4961</span>
      </li>
      <li>
        <svg viewBox="0 0 24 24" aria-hidden="true"><rect x="2" y="5" width="20" height="14" rx="2" fill="#e8a623"/><path d="M3 6l9 7 9-7" fill="none" stroke="#1f1f22" stroke-width="1.6"/></svg>
        <span>info@renwick-tolliver.co.uk</span>
      </li>
      <li>
        <svg viewBox="0 0 24 24" aria-hidden="true"><circle cx="12" cy="12" r="10" fill="#e8a623"/><path d="M2 12h20M12 2c3 3 3 17 0 20M12 2c-3 3-3 17 0 20" fill="none" stroke="#1f1f22" stroke-width="1.4"/></svg>
        <span>www.renwick-tolliver.co.uk</span>
      </li>
    </ul>

    <p class="address">Harrow Lane, Elmsbury Westford, WF4 2KD</p>
  </section>

</main>
</body>
</html>
```